PowerPoint Design for upcoming Broadcast

I need a PowerPoint design complete with all the templates in PPT, i.e two columns of text, one column of text with adjacent area for image, etc. Per the attached logo. Do not use the gold element in the design. 16x9

Target Market(s)

Business Leaders

Industry/Entity Type

Business Consultant

Other font styles liked:
• Arial

Colors

Designer to choose colors to be used in the design.

Requirements
Must have
• Crisp clean design. #for each color used.
Nice to have
• An assortment of charts in the ppt color schemes. A military (KVTF) theme.
Should not have
• Gaudy. Flashy. Transitions.

```html
<!DOCTYPE html>
<html lang="en">
<head>
<meta charset="utf-8">
<title>Project Name Title Here</title>
<link rel="stylesheet" href="https://fonts.googleapis.com/css2?family=Carlito:wght@400;700&family=Montserrat:wght@400;700&display=swap">
<style>
  :root {
    --red-deep: #7a0610;
    --red: #a50d1a;
    --red-bright: #c4121f;
    --silver: #d5d9de;
    --silver-dark: #b7bdc4;
    --title-red: #8e0a15;
    --body-grey: #8797a8;
    --footer-black: #141414;
    --stage: #e6e8eb;
    --white: #ffffff;
  }
  * { margin: 0; padding: 0; box-sizing: border-box; }
  html, body { width: 1200px; height: 900px; overflow: hidden; background: var(--stage); }

  .slide {
    position: absolute; left: 0; top: 112px; width: 1200px; height: 675px;
    overflow: hidden; background: var(--white);
    font-family: "Carlito", Calibri, sans-serif;
  }

  .header { position: absolute; left: 0; top: 0; width: 1200px; height: 86px; }
  .header svg { position: absolute; left: 0; top: 0; }
  .project-title {
    position: absolute; left: 18px; top: 15px;
    font-family: "Montserrat", Arial, sans-serif; font-weight: 700;
    font-size: 34px; line-height: 44px; color: var(--white); letter-spacing: -0.3px;
  }

  .brand-mark { position: absolute; left: 1062px; top: 6px; width: 124px; height: 124px; }
  .brand-mark .disc { position: absolute; inset: 0; border-radius: 50%; background: var(--red); border: 4px solid var(--silver); }
  .brand-mark .name {
    position: absolute; inset: 0; display: flex; align-items: center; justify-content: center;
    font-family: "Carlito", Calibri, sans-serif; font-weight: 700; font-size: 32px; color: var(--white);
  }

  .points { position: absolute; left: 0; top: 118px; width: 1200px; }
  .point { position: absolute; left: 0; width: 1200px; height: 136px; }
  .point-marker {
    position: absolute; left: 22px; top: 2px; width: 36px; height: 36px;
    border-radius: 50%; background: var(--red-bright); border: 3px solid var(--silver-dark);
  }
  .point-title {
    position: absolute; left: 68px; top: 0;
    font-weight: 700; font-size: 28px; line-height: 38px; color: var(--title-red);
  }
  .point-text {
    position: absolute; left: 68px; top: 38px; width: 1110px;
    font-size: 22px; line-height: 31px; color: var(--body-grey);
  }

  .footer {
    position: absolute; left: 0; top: 639px; width: 1200px; height: 36px;
    background: linear-gradient(#2a2a2a, var(--footer-black));
  }
  .copyright {
    position: absolute; left: 12px; top: 10px;
    font-family: "Montserrat", Arial, sans-serif; font-size: 14px; line-height: 16px;
    font-weight: 400; color: var(--white); letter-spacing: -0.2px;
  }
  .page-number {
    position: absolute; left: 1144px; top: 629px; width: 46px; height: 46px; border-radius: 50%;
    background: var(--red-deep); border: 3px solid var(--silver);
    display: flex; align-items: center; justify-content: center;
    font-family: "Montserrat", Arial, sans-serif; font-weight: 700; font-size: 18px; color: var(--white);
  }
</style>
</head>
<body>
<div class="slide">
  <header class="header">
    <svg width="1200" height="86" viewBox="0 0 1200 86" aria-hidden="true">
      <defs>
        <linearGradient id="band" x1="0" y1="0" x2="1" y2="0">
          <stop offset="0" stop-color="#8a0712"/>
          <stop offset="0.6" stop-color="#a00c18"/>
          <stop offset="1" stop-color="#b3111d"/>
        </linearGradient>
      </defs>
      <rect x="0" y="0" width="1200" height="74" fill="url(#band)"/>
      <polygon points="560,0 700,0 520,74 420,74" fill="#ffffff" opacity="0.04"/>
      <polygon points="780,0 880,0 760,74 690,74" fill="#ffffff" opacity="0.04"/>
      <polygon points="0,72 1200,66 1200,78 0,81" fill="var(--silver)"/>
      <polygon points="0,81 1200,78 1200,83 0,86" fill="var(--red-deep)"/>
    </svg>
    <h1 class="project-title">Project Name Title Here</h1>
  </header>

  <div class="brand-mark">
    <span class="disc"></span>
    <span class="name">KVTF</span>
  </div>

  <section class="points">
    <article class="point" style="top:0">
      <span class="point-marker"></span>
      <h2 class="point-title">Bullet Points Title Here</h2>
      <p class="point-text">Meridex's Target System Diagnostic Platform is a Controlled Flow-Through Rapid Immunoassay Test,<br>offering an array of improved modifications and features to the traditional Flow-Through Immuno-<br>assay Test. With its Platform uniformity, vacuum pump, absorption layer for sample overflow.</p>
    </article>
    <article class="point" style="top:160px">
      <span class="point-marker"></span>
      <h2 class="point-title">Bullet Points Title Here</h2>
      <p class="point-text">Meridex's Target System Diagnostic Platform is a Controlled Flow-Through Rapid Immunoassay Test,<br>offering an array of improved modifications and features to the traditional Flow-Through Immuno-<br>assay Test. With its Platform uniformity, vacuum pump, absorption layer for sample overflow.</p>
    </article>
    <article class="point" style="top:330px">
      <span class="point-marker"></span>
      <h2 class="point-title">Bullet Points Title Here</h2>
      <p class="point-text">Meridex's Target System Diagnostic Platform is a Controlled Flow-Through Rapid Immunoassay Test,<br>offering an array of improved modifications and features to the traditional Flow-Through Immuno-<br>assay Test. With its Platform uniformity, vacuum pump, absorption layer for sample overflow.</p>
    </article>
  </section>

  <footer class="footer">
    <span class="copyright">COPYRIGHT TEXT HERE</span>
  </footer>
  <div class="page-number">01</div>
</div>
</body>
</html>
```